Online media outlet needs a blog and logo

A new online blog platform is being established in the UK. The blog will be very similar in layout to www.quorvel.co. It will need to have a main story slider showing three slides and block tiles beneath the slider for additional tiles.

The blog platform will be called 'Tandrel Brisk' and will also need a professional looking logo design for the name.

The website should be designed in Word Press.

Industry/Entity Type

Media

Logo Text

Tandrel Brisk

Coding

Coded - Design and coding required

Number of Pages Required

3 page

Font styles to use
Other font styles liked:
• Helvetica

Requirements
Must have
• A slider showing three slides. Be similar to Quor V (see previous comment). Be Word Press compatible.

```html
<!DOCTYPE html>
<html lang="en">
<head>
<meta charset="utf-8">
<title>Tandrel Brisk</title>
<link href="https://fonts.googleapis.com/css2?family=Roboto:wght@300;400;500;700;900&display=swap" rel="stylesheet">
<style>
:root{
  --blue:#1f6fc4;
  --blue-dark:#154f93;
  --blue-light:#3d8ee0;
  --ink:#222;
  --muted:#888;
  --page:#eceef1;
  --white:#fff;
  --footer:#15171c;
}
*{box-sizing:border-box;margin:0;padding:0}
html,body{width:1200px;height:3248px;overflow:hidden}
body{position:relative;background:var(--page);font-family:'Roboto',Helvetica,Arial,sans-serif;color:var(--ink)}
.abs{position:absolute}

/* hero */
.hero{left:0;top:0;width:1200px;height:612px}
.hero-photo{position:absolute;inset:0;background:linear-gradient(180deg,#8a8f98 0%,#c9b79a 35%,#6d6a66 70%,#3a3a3c 100%)}
.topbar{position:absolute;left:0;top:0;width:1200px;height:64px;background:rgba(10,40,90,.55)}
.brand{position:absolute;left:60px;top:20px;font-weight:700;font-size:22px;color:var(--white);letter-spacing:.5px}
.social{position:absolute;top:20px;display:flex;gap:10px}
.social span{width:24px;height:24px;border-radius:50%;background:var(--white)}
.menu-btn{position:absolute;right:56px;top:14px;width:38px;height:36px;border:2px solid var(--white);border-radius:4px;display:flex;flex-direction:column;justify-content:center;align-items:center;gap:4px}
.menu-btn i{display:block;width:16px;height:2px;background:var(--white)}
.hero-title{position:absolute;left:0;width:1200px;top:270px;text-align:center;font-size:56px;font-weight:900;color:var(--white);letter-spacing:3px;text-transform:uppercase;text-shadow:0 2px 6px rgba(0,0,0,.4)}
.hero-sub{position:absolute;left:0;width:1200px;top:350px;text-align:center;font-size:22px;line-height:32px;color:var(--white)}
.hero-arrows{position:absolute;top:468px;left:560px;display:flex;gap:20px}
.hero-arrows span{width:32px;height:32px;border-radius:50%;border:2px solid rgba(255,255,255,.8)}

/* nav */
.nav{left:0;top:612px;width:1200px;height:58px;background:linear-gradient(180deg,var(--blue-light),var(--blue-dark));display:flex;padding-left:100px}
.nav a{color:var(--white);font-size:14px;font-weight:500;text-transform:uppercase;text-decoration:none;padding:0 26px;line-height:58px}
.nav a.active{background:rgba(255,255,255,.18);border-bottom:3px solid var(--white)}

/* cards */
.card{position:absolute;overflow:hidden;background:var(--white);box-shadow:0 1px 3px rgba(0,0,0,.12)}
.card .photo{position:absolute;inset:0}
.card .shade{position:absolute;inset:0;background:linear-gradient(180deg,rgba(0,0,0,0) 40%,rgba(0,0,0,.75) 100%)}
.tag{position:absolute;left:14px;top:12px;font-size:13px;font-weight:700;color:var(--white);text-transform:uppercase}
.text-card .tag{position:static;color:var(--ink);display:block;margin-bottom:10px}
.card .over{position:absolute;left:14px;right:14px;bottom:14px;color:var(--white)}
.over h3{font-size:20px;font-weight:500;line-height:25px;margin-bottom:10px}
.meta{font-size:12px;color:var(--muted)}
.over .meta{color:#ddd}
.text-card{padding:14px}
.text-card h3{font-size:20px;font-weight:500;line-height:26px;margin-bottom:12px}
.text-card p{font-size:13px;line-height:20px;color:#777;margin-bottom:16px}

.g-crowd{background:linear-gradient(160deg,#7a8aa0,#b45a4a 55%,#3b3f4a)}
.g-parl{background:linear-gradient(180deg,#1d4d9a,#6a86b8 50%,#c79a4a 80%,#3a2f2a)}
.g-castle{background:linear-gradient(180deg,#6aa2d8,#b9d3ea 40%,#8b7c63 65%,#4d5a36)}
.g-sky{background:linear-gradient(180deg,#1a3e86,#3d71bd 60%,#1c2f55)}
.g-street{background:linear-gradient(180deg,#c8c4bd,#8e8072 55%,#3c3733)}
.g-wheel{background:linear-gradient(180deg,#0d2a6e,#2d3f8a 50%,#a03a3a)}
.g-people{background:linear-gradient(160deg,#a88a6e,#d3b08e 50%,#4a3e35)}
.g-bus{background:linear-gradient(180deg,#b9c2cc,#b8322e 55%,#3a3a3a)}
.g-soldier{background:linear-gradient(180deg,#8c8a82,#5e5a50 60%,#2e2c28)}
.g-park{background:linear-gradient(180deg,#c7a05a,#6f7a3c 45%,#3b4a2a)}
.g-lane{background:linear-gradient(180deg,#d9d4cc,#7b6f66 50%,#2b2724)}

/* newsletter */
.news{left:0;top:1520px;width:1200px;height:240px;background:linear-gradient(180deg,#1c5fb0,#2c7bd0 50%,#1a56a4)}
.news h2{position:absolute;left:0;width:1200px;top:52px;text-align:center;font-size:26px;font-weight:400;color:var(--white)}
.news .field{position:absolute;left:348px;top:112px;width:298px;height:40px;background:var(--white);border-radius:2px;font-size:14px;color:#999;padding:0 12px;line-height:40px}
.news .btn{position:absolute;left:664px;top:112px;width:188px;height:40px;background:#0e3b78;color:var(--white);font-size:14px;text-align:center;line-height:40px;border-radius:2px}
.news .query{position:absolute;left:0;width:1200px;top:205px;text-align:center;font-size:15px;color:var(--white);text-decoration:underline}

/* footer */
.footer{left:0;top:2932px;width:1200px;height:316px;background:var(--footer)}
.footer h2{position:absolute;left:0;width:1200px;top:44px;text-align:center;font-size:24px;font-weight:700;color:var(--white)}
.f-links{position:absolute;left:0;width:1200px;top:134px;display:flex;justify-content:center}
.f-links a{color:#ddd;font-size:15px;text-decoration:none;padding:0 34px;border-left:1px solid #555}
.f-links a:first-child{border-left:none}
.f-social{position:absolute;left:0;width:1200px;top:190px;display:flex;justify-content:center;gap:24px}
.f-social span{width:44px;height:44px;border-radius:50%;border:2px solid #ccc}
.copy{position:absolute;left:0;width:1200px;top:276px;text-align:center;font-size:12px;color:#999}
</style>
</head>
<body>

<header class="abs hero">
  <div class="hero-photo" role="img" aria-label="City street with a domed building and pedestrians at sunset"></div>
  <div class="topbar">
    <div class="brand">TANDREL BRISK</div>
    <div class="social" style="left:840px"><span></span><span></span><span></span><span></span></div>
    <div class="menu-btn"><i></i><i></i><i></i></div>
  </div>
  <h1 class="hero-title">Tandrel Brisk</h1>
  <p class="hero-sub">Britain's Favourite Economic Journal, but our<br>Success is not assured</p>
  <div class="hero-arrows">
    <span><svg width="28" height="28" viewBox="0 0 28 28"><path d="M16 8l-6 6 6 6" fill="none" stroke="#fff" stroke-width="2"/></svg></span>
    <span><svg width="28" height="28" viewBox="0 0 28 28"><path d="M12 8l6 6-6 6" fill="none" stroke="#fff" stroke-width="2"/></svg></span>
  </div>
</header>

<nav class="abs nav">
  <a class="active">Current Topics</a><a>Tandrel Weekend</a><a>Government</a><a>Politics</a><a>Competition</a><a>Investment</a>
</nav>

<!-- section one -->
<article class="card" style="left:100px;top:732px;width:320px;height:268px">
  <div class="photo g-crowd" role="img" aria-label="Protesters holding signs at a rally"></div><div class="shade"></div>
  <span class="tag">Politics</span>
  <div class="over"><h3>Quis nostrum exercitationem ullam corporis</h3><div class="meta">Brisk Policy Desk - 3 May 2016</div></div>
</article>
<article class="card text-card" style="left:440px;top:732px;width:320px;height:268px">
  <span class="tag">Politics</span>
  <h3>Quasi architecto beatae vitae dicta sunt explicabo</h3>
  <p>Nam libero tempore cum soluta nobis est eligendi optio cumque nihil impedit quo minus id quod maxime placeat facere possimus omnis voluptas.</p>
  <div class="meta">Brisk Policy Desk - 3 May 2016</div>
</article>
<article class="card" style="left:780px;top:732px;width:320px;height:268px">
  <div class="photo g-parl" role="img" aria-label="Houses of Parliament at dusk"></div><div class="shade"></div>
  <span class="tag">Parliament</span>
  <div class="over"><h3>Quis autem vel eum iure reprehenderit qui in ea voluptate</h3><div class="meta">Brisk Policy Desk - 3 May 2016</div></div>
</article>

<article class="card" style="left:100px;top:1028px;width:660px;height:452px">
  <div class="photo g-castle" role="img" aria-label="Stone castle on a green hillside under blue sky"></div><div class="shade"></div>
  <span class="tag">Landscape</span>
  <div class="over"><h3>Civic Panel takes Transit Board to court over airport security: duis aute irure dolor in reprehenderit consequatur</h3><div class="meta">Brisk Policy Desk - 3 May 2016</div></div>
</article>
<article class="card" style="left:780px;top:1028px;width:320px;height:220px">
  <div class="photo g-sky" role="img" aria-label="City skyline under a deep blue sky"></div><div class="shade"></div>
  <span class="tag">Politics</span>
  <div class="over"><h3>Quis autem vel eum iure reprehenderit qui in ea</h3><div class="meta">Brisk Policy Desk - 3 May 2016</div></div>
</article>
<article class="card" style="left:780px;top:1272px;width:320px;height:208px">
  <div class="photo g-street" role="img" aria-label="Busy shopping street with pedestrians"></div><div class="shade"></div>
  <div class="over"><h3>Eaque ipsam nisi molestiae consequatur, vel illum qui dolorem</h3><div class="meta">Brisk Policy Desk - 3 May 2016</div></div>
</article>

<section class="abs news" role="img" aria-label="Blue city backdrop behind the newsletter signup">
  <h2>Join Thousands of Others and Enjoy With Tandrel Brisk</h2>
  <div class="field">Email</div>
  <div class="btn">Join Us Now</div>
  <div class="query">Any Queries? Click Here</div>
</section>

<!-- section two -->
<article class="card" style="left:100px;top:1828px;width:320px;height:272px">
  <div class="photo g-wheel" role="img" aria-label="Observation wheel lit at night by the river"></div><div class="shade"></div>
  <span class="tag">Politics</span>
  <div class="over"><h3>Quis autem vel eum iure repre henderit qui in ea</h3><div class="meta">Brisk Policy Desk - 3 May 2016</div></div>
</article>
<article class="card" style="left:440px;top:1828px;width:320px;height:272px">
  <div class="photo g-people" role="img" aria-label="Group of young people laughing together"></div><div class="shade"></div>
  <div class="over"><h3>Consequatur, vel illum qui dolorem eum fugiat quo voluptas</h3><div class="meta">Brisk Policy Desk - 3 May 2016</div></div>
</article>
<article class="card text-card" style="left:780px;top:1828px;width:320px;height:280px">
  <span class="tag">Politics</span>
  <h3>At vero eos et accusamus et iusto odio dignissimos</h3>
  <p>Nam libero tempore cum soluta nobis est eligendi optio cumque nihil impedit quo minus id quod maxime placeat facere possimus omnis voluptas.</p>
  <div class="meta">Brisk Policy Desk - 3 May 2016</div>
</article>

<article class="card" style="left:100px;top:2120px;width:320px;height:212px">
  <div class="photo g-bus" role="img" aria-label="Red double-decker bus on a city road"></div><div class="shade"></div>
  <div class="over"><h3>Quis nostrum exercitationem ullam corporis suscipit</h3><div class="meta">Brisk Policy Desk - 3 May 2016</div></div>
</article>
<article class="card" style="left:100px;top:2360px;width:320px;height:212px">
  <div class="photo g-soldier" role="img" aria-label="Uniformed officer standing on a street"></div><div class="shade"></div>
  <div class="over"><h3>Repudiandae sint et molestiae non recusandae</h3><div class="meta">Brisk Policy Desk - 3 May 2016</div></div>
</article>
<article class="card" style="left:440px;top:2120px;width:660px;height:452px">
  <div class="photo g-park" role="img" aria-label="Family walking a dog through an autumn park"></div><div class="shade"></div>
  <span class="tag">People</span>
  <div class="over"><h3>Temporibus autem quibusdam et aut officiis debitis aut rerum necessitatibus saepe eveniet ut et voluptates</h3><div class="meta">Brisk Policy Desk - 3 May 2016</div></div>
</article>

<article class="card text-card" style="left:100px;top:2600px;width:320px;height:272px">
  <span class="tag">Landscape</span>
  <h3>Tenetur a sapiente delectus, ut aut reiciendis voluptatibus</h3>
  <p>Nam libero tempore cum soluta nobis est eligendi optio cumque nihil impedit quo minus id quod maxime placeat facere possimus omnis voluptas.</p>
  <div class="meta">Brisk Policy Desk - 3 May 2016</div>
</article>
<article class="card" style="left:440px;top:2600px;width:320px;height:272px">
  <div class="photo g-lane" role="img" aria-label="Narrow old town lane with shopfronts"></div><div class="shade"></div>
  <div class="over"><h3>Civic Panel takes Transit Board to court over airport security</h3><div class="meta">Brisk Policy Desk - 3 May 2016</div></div>
</article>
<article class="card text-card" style="left:780px;top:2600px;width:320px;height:272px">
  <span class="tag">People</span>
  <h3>Alias consequatur aut perferen dis doloribus</h3>
  <p>Nam libero tempore cum soluta nobis est eligendi optio cumque nihil impedit quo minus id quod maxime placeat facere possimus omnis voluptas.</p>
  <div class="meta">Brisk Policy Desk - 3 May 2016</div>
</article>

<footer class="abs footer">
  <h2>TANDREL BRISK</h2>
  <div class="f-links"><a>Introduction</a><a>Our Blog</a><a>All Topics</a><a>About Us</a><a>Contact Us</a></div>
  <div class="f-social"><span></span><span></span><span></span><span></span></div>
  <div class="copy">Copyright 2016. Tandrel Brisk. All rights reserved.</div>
</footer>

</body>
</html>
```